Lumora Systems New Website - IT Infrastructure | Smart Cabinet | Micro Data Center

We're an IT SI providing Server Room Design & Build | All-in-One Rack & Smart Cabinet | Structured Cabling | IT Relocation | Maintenance. Old website can be found at www.lumorasys.com.hk. We'd like a brand new wix website which is modern, minimalist, interactive with some animation. Website content will be mostly static and include our service, our project, news and events, about us, contacts, blogs, partners and brands, etc.

reference sites:
We'd like to see more designs referring to below

https://www.pixelvane.example/design/41736205
https://www.pixelvane.example/design/41892417
https://velbrinn.example/

Animation (scrolling effect) referring to
https://velbrinn.example/intelligence/smart-office-room/
Updates

we'd like below style.

Designs look the same

Target Market(s)

Commercials in HK

Industry/Entity Type

IT, Technology, Data Center

Coding

Coded - Design and coding required

Font styles to use
Sans Serif

Requirements
Must have
• CMS, Some Interactive Elements/ Graphics

```html
<!DOCTYPE html>
<html lang="en">
<head>
<meta charset="UTF-8">
<title>Lumora Systems – IT Infrastructure</title>
<link rel="stylesheet" href="https://fonts.googleapis.com/css2?family=Roboto:wght@400;500;700&family=Lato:wght@400;700&display=swap">
<style>
:root{
  --red:#d8321e;
  --navy:#111a33;
  --navy-2:#1a2342;
  --ink:#1b1b1b;
  --muted:#8a8a8a;
  --light:#f3f3f3;
  --card:#efefef;
  --footer:#1e1e1e;
  --white:#fff;
}
*{box-sizing:border-box;margin:0;padding:0}
html,body{width:1200px;height:4539px;overflow:hidden}
body{font-family:"Lato",sans-serif;color:var(--ink);background:var(--white);position:relative}
section,footer{position:absolute;left:0;width:1200px;overflow:hidden}
.abs{position:absolute}
h1,h2,h3,h4{font-family:"Roboto",sans-serif}
.tag{position:absolute;font-size:9px;color:#333;background:#e6e6e6;padding:2px 6px 2px 5px;border-left:3px solid var(--red);white-space:nowrap}
.tag.dark{background:#2a3352;color:#dfe2ea}
.title{position:absolute;left:0;width:1200px;text-align:center;font-size:36px;font-weight:700;color:var(--ink)}
.title em,.red{color:var(--red);font-style:normal}
.btn{position:absolute;background:var(--red);color:#fff;font-size:10px;font-weight:700;display:flex;align-items:center;justify-content:center;font-family:"Roboto",sans-serif}
.btn.outline{background:#fff;color:var(--red);border:1px solid var(--red)}

/* hero */
.hero{top:0;height:574px;background:linear-gradient(100deg,#1c2250 0%,#2a2f5c 45%,#3a3d52 100%)}
.hero-photo{position:absolute;inset:0;background:linear-gradient(90deg,rgba(20,24,60,.2),rgba(70,75,95,.5) 60%,rgba(30,32,45,.7))}
.logo{position:absolute;display:flex;align-items:center;gap:8px;font-family:"Roboto",sans-serif;font-weight:500;font-size:22px;color:#fff}
.logo i{display:block;width:24px;height:24px;border:2px solid #fff}
.nav{position:absolute;top:44px;left:0;width:1200px;font-size:12px;color:#fff;font-family:"Roboto",sans-serif;font-weight:500}
.nav span{position:absolute}
.nav .on{color:var(--red)}
.nav .sep{top:0;width:1px;height:14px;background:rgba(255,255,255,.5)}
.hero h1{position:absolute;left:151px;top:204px;font-size:38px;line-height:50px;font-weight:500;color:#fff;width:560px}
.hero p{position:absolute;left:151px;top:312px;width:470px;font-size:11.5px;line-height:18.5px;color:#dde0ea}

/* why */
.why{top:574px;height:462px;background:var(--light)}
.feat{position:absolute;width:260px;display:flex;gap:14px}
.feat svg{flex:none}
.feat h4{font-size:13px;font-weight:500;margin:2px 0 6px}
.feat p{font-size:10.5px;line-height:15px;color:var(--muted)}

/* services */
.services{top:1036px;height:426px;background:#fff}
.svc{position:absolute;top:182px;width:254px;height:142px;background:var(--card);padding:32px 40px}
.svc b{display:block;font-family:"Roboto",sans-serif;font-size:26px;font-weight:400;color:var(--red);margin-bottom:16px}
.svc span{font-size:13.5px;line-height:21px;color:#444}
.svc.active{background:var(--red)}
.svc.active b,.svc.active span{color:#fff}

/* about */
.about{top:1462px;height:555px;background:var(--navy)}
.about h2{position:absolute;left:245px;top:76px;font-size:36px;line-height:50px;font-weight:500;color:#fff}
.about .lead{position:absolute;left:629px;top:88px;width:340px;font-size:11.5px;line-height:19px;color:#dfe2ea}
.about .lh{position:absolute;left:629px;top:222px;font-size:12px;font-weight:700;color:#fff}
.checks{position:absolute;left:629px;top:258px;list-style:none}
.checks li{display:flex;align-items:center;gap:15px;font-size:10.5px;color:#b8bdcc;height:23.6px}

/* projects */
.projects{top:2017px;height:485px;background:#fff}
.proj{position:absolute;top:171px;width:194px;height:212px;background:#fff;border:1px solid #eee}
.proj .ph{height:102px;background:linear-gradient(180deg,#3c4563,#7b8298 55%,#5a6078)}
.proj h4{font-size:13.5px;line-height:18px;font-weight:400;color:#333;padding:12px 10px 0;height:54px}
.proj .btn{left:10px;width:172px;height:30px;bottom:14px}
.proj.lift{box-shadow:0 4px 14px rgba(0,0,0,.15)}

/* news */
.news{top:2502px;height:786px;background:var(--light)}
.post{position:absolute;left:370px;width:460px;height:158px;border-bottom:1px solid #d2d2d2}
.post .ph{position:absolute;left:0;top:0;width:148px;height:148px;background:linear-gradient(180deg,#39405a,#7d8399 50%,#555b70)}
.post .txt{position:absolute;left:166px;top:14px;width:290px}
.post small{font-size:9px;color:var(--muted)}
.post h4{font-size:13.5px;font-weight:500;margin:10px 0 8px}
.post p{font-size:9.5px;line-height:14px;color:var(--muted)}
.post a{display:block;margin-top:8px;font-size:10px;color:var(--red);text-decoration:none}

/* partners */
.partners{top:3288px;height:359px;background:#fff}
.badge{position:absolute;top:183px;height:34px;background:#c9c9c9;border-radius:4px}

/* contact */
.contact{top:3647px;height:626px;background:var(--navy)}
.contact h2{position:absolute;left:233px;top:84px;font-size:36px;line-height:50px;font-weight:500;color:#fff}
.addr{position:absolute;left:233px;top:208px;display:flex;gap:14px;align-items:center;font-size:9px;line-height:12px;color:#cfd3df;width:340px}
.map{position:absolute;left:233px;top:254px;width:340px;height:212px;background:linear-gradient(135deg,#e6e3dc,#d6dfe4 60%,#e2e0d8)}
.contact .lead{position:absolute;left:640px;top:102px;width:330px;font-size:11px;line-height:19px;color:#dfe2ea}
.field{position:absolute;left:640px;width:328px;height:36px;border:1px solid #8a90a6;color:#dfe2ea;font-size:10px;font-weight:700;padding:12px 14px}

/* footer */
.site-footer{top:4273px;height:266px;background:var(--footer);color:#cfcfcf}
.site-footer h4{position:absolute;top:53px;font-size:11.5px;font-weight:500;color:#fff}
.flist{position:absolute;top:82px;list-style:none;font-size:8.5px;line-height:11px;color:#aaa}
.flist li{margin-bottom:22px}
.fcontact{position:absolute;left:888px;top:82px;list-style:none;font-size:8px;line-height:10.5px;color:#aaa}
.fcontact li{display:flex;gap:14px;margin-bottom:14px}
.fcontact svg{flex:none}
</style>
</head>
<body>

<section class="hero">
  <div class="hero-photo" role="img" aria-label="Server racks in a dim data center aisle"></div>
  <div class="logo" style="left:160px;top:36px"><i></i>Lumora</div>
  <nav class="nav">
    <span class="on" style="left:622px">Home</span>
    <span class="sep" style="left:666px"></span>
    <span style="left:694px">About Us</span>
    <span class="sep" style="left:760px"></span>
    <span style="left:784px">Our Services</span>
    <span class="sep" style="left:870px"></span>
    <span style="left:892px">Our Projects</span>
    <span class="sep" style="left:980px"></span>
    <span style="left:1004px">Contact</span>
  </nav>
  <span class="tag dark" style="left:151px;top:184px;background:transparent">The #Best Technical Solutions Provider</span>
  <h1>Design Your IT Infrastructure Solution with the Best</h1>
  <p>We deliver the best in Data Center Infrastructure, Network Infrastructure, Structured Cabling, Telephony, Access Control, Video Surveillance, Audiovisual &amp; Conferencing, Relocation &amp; Migration and Maintenance solutions.</p>
  <div class="btn" style="left:151px;top:398px;width:127px;height:37px">Explore More</div>
</section>

<section class="why">
  <span class="tag" style="left:557px;top:50px">Why We Special</span>
  <h2 class="title" style="top:72px">Why We <em>Special</em></h2>
  <div class="feat" style="left:308px;top:168px">
    <svg width="44" height="48" viewBox="0 0 44 48" fill="none" stroke="#333" stroke-width="1.5"><circle cx="22" cy="20" r="10"/><path d="M17 32h10M18 37h8M22 4v4M8 20H4M40 20h-4M11 9l3 3M33 9l-3 3"/><circle cx="22" cy="20" r="4" stroke="var(--red)"/></svg>
    <div><h4>Comprehensive Expertise</h4><p>Lorem ipsum dolor sit amet, consectetur adipiscing elit. Amet proin ut vitae, felis. Mauris aliquet faucibus iaculis dui vitae ullamcorper ac.</p></div>
  </div>
  <div class="feat" style="left:634px;top:168px">
    <svg width="48" height="48" viewBox="0 0 48 48" fill="none" stroke="#333" stroke-width="1.5"><circle cx="24" cy="10" r="7" stroke="var(--red)"/><path d="M21 10l2 2 4-4" stroke="var(--red)"/><path d="M4 28l10-8 10 6 10-6 10 8-14 12-6-4-6 4z"/></svg>
    <div><h4>Recognition &amp; Trust</h4><p>Lorem ipsum dolor sit amet, consectetur adipiscing elit. Amet proin ut vitae, felis. Mauris aliquet faucibus iaculis dui vitae ullamcorper ac.</p></div>
  </div>
  <div class="feat" style="left:304px;top:290px">
    <svg width="48" height="48" viewBox="0 0 48 48" fill="none" stroke="#333" stroke-width="1.5"><circle cx="24" cy="16" r="10" stroke="var(--red)"/><path d="M24 10v12M21 13h5a2 2 0 010 4h-4a2 2 0 000 4h5" stroke="var(--red)"/><path d="M4 22v12l10 10M44 22v12L34 44"/></svg>
    <div><h4>Cost-Effective Solutions</h4><p>Lorem ipsum dolor sit amet, consectetur adipiscing elit. Amet proin ut vitae, felis. Mauris aliquet faucibus iaculis dui vitae ullamcorper ac.</p></div>
  </div>
  <div class="feat" style="left:634px;top:290px">
    <svg width="48" height="48" viewBox="0 0 48 48" fill="none" stroke="#333" stroke-width="1.5"><circle cx="24" cy="6" r="4"/><circle cx="24" cy="26" r="8" stroke="var(--red)"/><circle cx="6" cy="40" r="4"/><circle cx="42" cy="40" r="4"/><path d="M24 10v8M12 36l6-4M36 36l-6-4"/></svg>
    <div><h4>Dedicated &amp; Supportive Team</h4><p>Lorem ipsum dolor sit amet, consectetur adipiscing elit. Amet proin ut vitae, felis. Mauris aliquet faucibus iaculis dui vitae ullamcorper ac.</p></div>
  </div>
</section>

<section class="services">
  <span class="tag" style="left:563px;top:76px">What We Do</span>
  <h2 class="title" style="top:96px">Our Services</h2>
  <div class="svc active" style="left:85px"><b>01.</b><span>Data Center Design &amp;<br>Build</span>
    <svg class="abs" style="right:18px;top:44px" width="38" height="10" viewBox="0 0 38 10" fill="none" stroke="#fff" stroke-width="1.3"><path d="M0 5h36M32 1l4 4-4 4"/></svg></div>
  <div class="svc" style="left:344px"><b>02.</b><span>Structured cabling &amp;<br>fiber backbone</span></div>
  <div class="svc" style="left:603px"><b>03.</b><span>All-In-One Rack /<br>Micro-Data Center</span></div>
  <div class="svc" style="left:862px"><b>04.</b><span>Audiovisual and<br>Conference Room</span></div>
</section>

<section class="about">
  <span class="tag dark" style="left:245px;top:55px">Who We Are</span>
  <h2>About<br><span class="red">Lumora</span> Systems</h2>
  <div class="abs" role="img" aria-label="Close-up of a network cable with miniature worker figures" style="left:245px;top:219px;width:259px;height:248px;background:linear-gradient(135deg,#6b5a8c,#c8b23a 45%,#d9d9dd 75%,#7f8a9a)"></div>
  <p class="lead">We deliver the best in Data Center Infrastructure, Network Infrastructure, Structured Cabling, Telephony, Access Control, Video Surveillance, Audiovisual &amp; Conferencing, Relocation &amp; Migration and Maintenance solutions.</p>
  <p class="lh">LUMORA's solution at-a-glance includes;</p>
  <ul class="checks">
    <li><svg width="9" height="8" viewBox="0 0 9 8" fill="none" stroke="#d8321e" stroke-width="1.5"><path d="M1 4l2.5 2.5L8 1"/></svg>Data Center / Server Room Design and Build</li>
    <li><svg width="9" height="8" viewBox="0 0 9 8" fill="none" stroke="#d8321e" stroke-width="1.5"><path d="M1 4l2.5 2.5L8 1"/></svg>Structured Cabling Solution</li>
    <li><svg width="9" height="8" viewBox="0 0 9 8" fill="none" stroke="#d8321e" stroke-width="1.5"><path d="M1 4l2.5 2.5L8 1"/></svg>Data and Voice Networks, IP-Telephony Solution</li>
    <li><svg width="9" height="8" viewBox="0 0 9 8" fill="none" stroke="#d8321e" stroke-width="1.5"><path d="M1 4l2.5 2.5L8 1"/></svg>WiFi Solution</li>
    <li><svg width="9" height="8" viewBox="0 0 9 8" fill="none" stroke="#d8321e" stroke-width="1.5"><path d="M1 4l2.5 2.5L8 1"/></svg>Relocation and Migration Service</li>
    <li><svg width="9" height="8" viewBox="0 0 9 8" fill="none" stroke="#d8321e" stroke-width="1.5"><path d="M1 4l2.5 2.5L8 1"/></svg>AV and Conference Room System</li>
  </ul>
  <div class="btn" style="left:629px;top:432px;width:126px;height:37px">Explore More</div>
</section>

<section class="projects">
  <span class="tag" style="left:546px;top:66px">What We Have Done</span>
  <h2 class="title" style="top:86px">Our <em>Projects</em></h2>
  <div class="proj" style="left:201px"><div class="ph" role="img" aria-label="Empty data hall with raised floor"></div><h4>A renowned China based listed insurance company</h4><div class="btn outline">Explore More</div></div>
  <div class="proj lift" style="left:402px"><div class="ph" role="img" aria-label="Empty data hall with raised floor"></div><h4>Global Tradelink</h4><div class="btn">Explore More</div></div>
  <div class="proj" style="left:603px"><div class="ph" role="img" aria-label="Empty data hall with raised floor"></div><h4>Harbourline Capital &amp; Meridian Life</h4><div class="btn outline">Explore More</div></div>
  <div class="proj" style="left:804px"><div class="ph" role="img" aria-label="Empty data hall with raised floor"></div><h4>A renowned China based Securities firm</h4><div class="btn outline">Explore More</div></div>
</section>

<section class="news">
  <span class="tag" style="left:572px;top:55px">Our Blogs</span>
  <h2 class="title" style="top:74px">News &amp; Events</h2>
  <article class="post" style="top:169px"><div class="ph" role="img" aria-label="Data hall interior"></div><div class="txt"><small>23 December 2023</small><h4>Title of the News or Event Post</h4><p>Lorem ipsum dolor sit amet, consecter adipiscing elit. Amet proin ut vita, felis. Mauris aliquet faucibus iaculis dui vitae ullamcorper ac.</p><a>Read More</a></div></article>
  <article class="post" style="top:342px"><div class="ph" role="img" aria-label="Data hall interior"></div><div class="txt"><small>23 December 2023</small><h4>Title of the News or Event Post</h4><p>Lorem ipsum dolor sit amet, consecter adipiscing elit. Amet proin ut vita, felis. Mauris aliquet faucibus iaculis dui vitae ullamcorper ac.</p><a>Read More</a></div></article>
  <article class="post" style="top:515px;border-bottom:none"><div class="ph" role="img" aria-label="Data hall interior"></div><div class="txt"><small>23 December 2023</small><h4>Title of the News or Event Post</h4><p>Lorem ipsum dolor sit amet, consecter adipiscing elit. Amet proin ut vita, felis. Mauris aliquet faucibus iaculis dui vitae ullamcorper ac.</p><a>Read More</a></div></article>
  <div class="btn" style="left:552px;top:700px;width:97px;height:35px">View All</div>
</section>

<section class="partners">
  <span class="tag" style="left:568px;top:83px">Featured In</span>
  <h2 class="title" style="top:120px">Our <em>Partners</em></h2>
  <div class="badge" style="left:176px;width:128px"></div>
  <div class="badge" style="left:354px;width:132px"></div>
  <div class="badge" style="left:536px;width:148px"></div>
  <div class="badge" style="left:728px;width:138px"></div>
  <div class="badge" style="left:906px;width:122px"></div>
  <div class="btn outline" style="left:552px;top:248px;width:97px;height:36px">View All</div>
</section>

<section class="contact">
  <span class="tag dark" style="left:233px;top:59px">Contact Us</span>
  <h2>Get in Touch<br>with Us</h2>
  <div class="addr"><svg width="24" height="24" viewBox="0 0 24 24"><circle cx="12" cy="12" r="12" fill="#e4e6ee"/><path d="M12 6a4 4 0 00-4 4c0 3 4 8 4 8s4-5 4-8a4 4 0 00-4-4z" fill="#111a33"/><circle cx="12" cy="10" r="1.4" fill="#e4e6ee"/></svg>Rm 1208, 12/F, Harbour Link Centre, 18 Wing Kei Road,<br>Kwun Tong, Kowloon, Hong Kong</div>
  <div class="map" role="img" aria-label="Street map showing the office location"></div>
  <p class="lead">Lorem ipsum dolor sit amet, consectetur adipiscing elit. Amet proin ut vitae, felis. Mauris aliquet faucibus iaculis dui vitae ullamcorper ac</p>
  <div class="field" style="top:196px">Your name*</div>
  <div class="field" style="top:254px">Email*</div>
  <div class="field" style="top:314px">Subject*</div>
  <div class="field" style="top:372px;height:95px">Your Message</div>
  <div class="btn" style="left:640px;top:492px;width:95px;height:35px">Submit</div>
</section>

<footer class="site-footer">
  <div class="logo" style="left:152px;top:36px;font-size:20px"><i></i>Lumora</div>
  <p class="abs" style="left:152px;top:107px;width:195px;font-size:8px;line-height:10.5px;color:#bbb">Lorem ipsum dolor sit amet consectetur. Mi nibh venenatis in suscipit turpis enim cursus vulputate amet. Lobortis mi platea aliquam senectus tempus mauris neque.</p>
  <div class="abs" style="left:152px;top:163px;display:flex;gap:10px">
    <span style="width:12px;height:12px;border-radius:50%;background:#ddd"></span>
    <span style="width:12px;height:12px;border-radius:50%;background:#ddd"></span>
    <span style="width:12px;height:12px;background:#ddd"></span>
  </div>
  <h4 style="left:456px">Website Links</h4>
  <ul class="flist" style="left:456px"><li>Home</li><li>About Us</li><li>Our Projects</li><li>FAQs</li></ul>
  <h4 style="left:648px">Services</h4>
  <ul class="flist" style="left:648px;width:120px"><li style="margin-bottom:12px">Website Data Center Design &amp; Build</li><li style="margin-bottom:12px">Structured cabling and fiber backbone</li><li style="margin-bottom:12px">All-In-One Rack / Micro-Data Center</li><li>Audiovisual and Conference Room</li></ul>
  <h4 style="left:888px">Contact Us</h4>
  <ul class="fcontact">
    <li><svg width="10" height="12" viewBox="0 0 10 12"><path d="M5 0a4 4 0 00-4 4c0 3 4 8 4 8s4-5 4-8a4 4 0 00-4-4z" fill="#ddd"/></svg><span>Rm 1208, 12/F, Harbour Link Centre,<br>18 Wing Kei Road, Kwun Tong,<br>Kowloon, Hong Kong</span></li>
    <li><svg width="10" height="8" viewBox="0 0 10 8"><rect width="10" height="8" fill="#ddd"/><path d="M0 0l5 4 5-4" stroke="#1e1e1e" fill="none"/></svg><span>hello@lumorasys.com.hk</span></li>
    <li><svg width="10" height="10" viewBox="0 0 10 10"><path d="M2 0l2 2-1 2 3 3 2-1 2 2-2 2C4 10 0 6 0 2z" fill="#ddd"/></svg><span>+852 2460 7315 /<br>+852 5318 4402</span></li>
    <li><svg width="10" height="10" viewBox="0 0 10 10"><rect y="3" width="10" height="7" fill="#ddd"/><rect x="2" width="6" height="3" fill="#ddd"/></svg><span>+852 2460 7390</span></li>
  </ul>
  <div class="abs" style="left:152px;top:213px;width:896px;height:1px;background:#444"></div>
  <p class="abs" style="left:0;top:236px;width:1200px;text-align:center;font-size:8px;color:#bbb">Non Copyrighted © 2022 Design and upload by corvel studio</p>
</footer>

</body>
</html>
```